Indoor Air Restoration company needs graphic design for a 6x12 v nose trailer to wrap

We offer mold services, duct cleaning, water damage clean up and odor removal. "We find, fix and prevent mold, odor and allergen problems" is what we want to communicate on this trailer, which is a rolling billboard. We like the blue and orange color themes, as found in our logo. The company name is Brightwater Dwelling Services and the logo is attached below. We'd like to see our message clearly, company name and what we offer. We tend to lean towards white letters on a darker background (blue or orange) but are very open to outside ideas, as we are stuck! Our website is available for reference if that is helpful. www.brightwaterdwell.com The phone number to be printed on truck is 302-517-9046, Happy designing!!

Target Market(s)

Home owners

Industry/Entity Type

Indoor Air Quality, Mold Remediation

Font styles to use
Sans Serif

Colors
0054AA
0677BA
7BADD7
CADEEF
E8F1F8
F0912C
F2A743
F7CA91
FBE8D2
FDF5EE

Requirements
Must have
• our message, company name and phone
Nice to have
• services we offer (mold remediation, duct cleaning, water damage and odor removal
Should not have
• cartoon feel

```html
<!DOCTYPE html>
<html lang="en">
<head>
<meta charset="utf-8">
<title>Brightwater Dwelling Services – Trailer Wrap Panels</title>
<link rel="stylesheet" href="https://fonts.googleapis.com/css2?family=Oswald:wght@500;600&family=Montserrat:ital,wght@0,400;0,500;1,800&family=Yellowtail&display=swap">
<style>
  :root {
    --stage: #5e5f62;
    --navy: #1c1c2b;
    --blue: #0677BA;
    --blue-deep: #0054AA;
    --blue-soft: #7BADD7;
    --blue-script: #2f8fd8;
    --orange: #F0912C;
    --orange-light: #F2A743;
    --white: #ffffff;
    --block-blue: #1f6fc0;
    --block-green: #2e9a3e;
    --block-red: #b0232a;
    --block-orange: #f29a2c;
  }
  * { box-sizing: border-box; margin: 0; padding: 0; }
  html, body { width: 1200px; height: 3000px; overflow: hidden; }
  body { background: var(--stage); position: relative; font-family: "Montserrat", sans-serif; color: var(--white); }

  .panel { position: absolute; background: var(--navy); overflow: hidden; }
  .panel-art { position: absolute; inset: 0; width: 100%; height: 100%; }
  .panel > * { position: absolute; }

  .message {
    font-family: "Montserrat", sans-serif; font-style: italic; font-weight: 800;
    text-transform: uppercase; line-height: 1.05; color: var(--white); white-space: nowrap;
  }
  .message .problems { color: var(--orange); }

  .brand-name {
    font-family: "Oswald", sans-serif; font-weight: 500; text-transform: uppercase;
    color: var(--white); line-height: 1.02; letter-spacing: 0.5px; white-space: nowrap;
  }
  .phone { font-family: "Oswald", sans-serif; font-weight: 600; line-height: 1; letter-spacing: 0.5px; white-space: nowrap; }
  .phone .dash { color: var(--orange); }
  .website { font-family: "Montserrat", sans-serif; font-weight: 400; color: var(--blue-soft); white-space: nowrap; }
  .website .tld { color: var(--orange); }

  .services { display: flex; align-items: center; gap: 18px; }
  .service-list { list-style: none; font-weight: 500; line-height: 1.2; flex: none; }
  .service-list li { display: flex; align-items: center; gap: 10px; white-space: nowrap; }
  .service-list li::before {
    content: ""; width: 0.42em; height: 0.42em; border-radius: 50%; background: var(--orange); flex: none;
  }
  .sign-off {
    font-family: "Yellowtail", cursive; color: var(--blue-script); line-height: 0.95;
    transform: rotate(-14deg); white-space: nowrap; flex: none;
  }
  .on-blue .website { color: #cfe4f5; }
  .on-blue .sign-off { color: #7fc0f0; }
  .centered { text-align: center; left: 0; right: 0; }
  .centered.services { justify-content: center; }

  .door-blocks { position: absolute; left: 900px; top: 720px; width: 260px; height: 560px; display: flex; flex-direction: column; gap: 20px; }
  .door-block { flex: 1; }
  .door-block.water { background: linear-gradient(180deg, #2a86d6, var(--block-blue)); }
  .door-block.allergen { background: linear-gradient(180deg, #3fb04d, var(--block-green)); }
  .door-block.heat { background: linear-gradient(180deg, #c8313a, var(--block-red)); }
  .door-block.airflow { background: linear-gradient(180deg, #f7b14a, var(--block-orange)); }
</style>
</head>
<body>

<!-- Side panel: large name with blue contact field -->
<section class="panel side-main" style="left:40px; top:40px; width:1120px; height:640px;">
  <svg class="panel-art" viewBox="0 0 1120 640" preserveAspectRatio="none" aria-hidden="true">
    <defs>
      <linearGradient id="sweep-a" x1="0" y1="0" x2="1" y2="0">
        <stop offset="0" stop-color="#F0912C" stop-opacity="0"/>
        <stop offset="0.6" stop-color="#F2A743" stop-opacity="0.85"/>
        <stop offset="1" stop-color="#F0912C"/>
      </linearGradient>
      <linearGradient id="blue-a" x1="0" y1="0" x2="1" y2="1">
        <stop offset="0" stop-color="#0677BA"/>
        <stop offset="1" stop-color="#0054AA"/>
      </linearGradient>
    </defs>
    <polygon points="300,300 640,290 640,470 300,470" fill="url(#sweep-a)"/>
    <polygon points="650,210 1120,210 1120,640 790,640 615,380" fill="#F0912C"/>
    <polygon points="680,232 1120,232 1120,640 815,640 648,385" fill="url(#blue-a)"/>
  </svg>
  <p class="message" style="right:40px; top:40px; text-align:right; font-size:30px;">
    We find fix and prevent mold, odor,<br>&amp; allergen <span class="problems" style="font-size:48px;">Problems</span>?
  </p>
  <p class="brand-name" style="left:60px; top:300px; font-size:66px;">Brightwater<br>Dwelling Services</p>
  <div class="on-blue" style="left:745px; top:265px; width:360px;">
    <p class="phone" style="font-size:58px;">302<span class="dash">-</span>517<span class="dash">-</span>9046</p>
    <p class="website" style="font-size:17px; margin-top:10px;">https://www.brightwaterdwell<span class="tld">.com</span></p>
    <div class="services" style="margin-top:28px;">
      <ul class="service-list" style="font-size:23px;">
        <li>Moisture</li><li>Mold</li><li>Odor</li><li>Duct Cleaning</li>
      </ul>
      <span class="sign-off" style="font-size:30px;">Happy<br>Designing!!</span>
    </div>
  </div>
</section>

<!-- Side panel: message over blue contact field -->
<section class="panel side-door" style="left:40px; top:720px; width:840px; height:560px;">
  <svg class="panel-art" viewBox="0 0 840 560" preserveAspectRatio="none" aria-hidden="true">
    <defs>
      <linearGradient id="blue-b" x1="0" y1="0" x2="1" y2="1">
        <stop offset="0" stop-color="#0677BA"/>
        <stop offset="1" stop-color="#0054AA"/>
      </linearGradient>
      <linearGradient id="sweep-b" x1="0" y1="0" x2="1" y2="0">
        <stop offset="0" stop-color="#F0912C"/>
        <stop offset="1" stop-color="#F2A743" stop-opacity="0"/>
      </linearGradient>
    </defs>
    <polygon points="440,290 640,290 640,400 440,400" fill="url(#sweep-b)"/>
    <polygon points="0,185 385,185 480,340 285,560 0,560" fill="#F0912C"/>
    <polygon points="0,205 372,205 458,340 262,560 0,560" fill="url(#blue-b)"/>
  </svg>
  <p class="message" style="left:36px; top:38px; font-size:27px;">
    We find fix and prevent mold, odor,<br>&amp; allergen <span class="problems" style="font-size:44px;">Problems</span>?
  </p>
  <div class="on-blue" style="left:36px; top:228px; width:380px;">
    <p class="phone" style="font-size:54px;">302<span class="dash">-</span>517<span class="dash">-</span>9046</p>
    <p class="website" style="font-size:17px; margin-top:8px;">https://www.brightwaterdwell<span class="tld">.com</span></p>
    <div class="services" style="margin-top:22px;">
      <ul class="service-list" style="font-size:22px;">
        <li>Moisture</li><li>Mold</li><li>Odor</li><li>Duct Cleaning</li>
      </ul>
      <span class="sign-off" style="font-size:28px;">Happy<br>Designing!!</span>
    </div>
  </div>
  <p class="brand-name" style="left:490px; top:290px; width:330px; text-align:center; font-size:38px;">Brightwater<br>Dwelling Services</p>
</section>

<div class="door-blocks">
  <div class="door-block water" role="img" aria-label="Blue door block with a water droplet icon"></div>
  <div class="door-block allergen" role="img" aria-label="Green door block with an allergen particle icon"></div>
  <div class="door-block heat" role="img" aria-label="Red door block with a flame icon"></div>
  <div class="door-block airflow" role="img" aria-label="Orange door block with a fan icon"></div>
</div>

<!-- Rear doors panel -->
<section class="panel rear" style="left:40px; top:1320px; width:540px; height:820px;">
  <p class="message centered" style="top:48px; font-size:22px;">
    We find fix and prevent mold, odor,<br>&amp; allergen <span class="problems" style="font-size:36px;">Problems</span>?
  </p>
  <p class="brand-name centered" style="top:190px; font-size:52px;">Brightwater<br>Dwelling Services</p>
  <p class="phone centered" style="top:375px; font-size:66px;">302<span class="dash">-</span>517<span class="dash">-</span>9046</p>
  <p class="website centered" style="top:462px; font-size:22px;">https://www.brightwaterdwell<span class="tld">.com</span></p>
  <div class="services centered" style="top:530px;">
    <ul class="service-list" style="font-size:24px;">
      <li>Moisture</li><li>Mold</li><li>Odor</li><li>Duct Cleaning</li>
    </ul>
    <span class="sign-off" style="font-size:32px;">Happy<br>Designing!!</span>
  </div>
</section>

<!-- Nose panel, left -->
<section class="panel nose-left" style="left:620px; top:1320px; width:540px; height:820px;">
  <p class="brand-name centered" style="top:150px; font-size:56px;">Brightwater<br>Dwelling Services</p>
  <p class="phone centered" style="top:340px; font-size:60px;">302<span class="dash">-</span>517<span class="dash">-</span>9046</p>
  <p class="website centered" style="top:420px; font-size:21px;">https://www.brightwaterdwell<span class="tld">.com</span></p>
  <div class="services centered" style="top:500px;">
    <ul class="service-list" style="font-size:26px;">
      <li>Moisture</li><li>Mold</li><li>Odor</li><li>Duct Cleaning</li>
    </ul>
    <span class="sign-off" style="font-size:34px;">Happy<br>Designing!!</span>
  </div>
</section>

<!-- Nose panel, right -->
<section class="panel nose-right" style="left:340px; top:2180px; width:520px; height:780px;">
  <p class="brand-name centered" style="top:140px; font-size:54px;">Brightwater<br>Dwelling Services</p>
  <p class="phone centered" style="top:325px; font-size:58px;">302<span class="dash">-</span>517<span class="dash">-</span>9046</p>
  <p class="website centered" style="top:402px; font-size:20px;">https://www.brightwaterdwell<span class="tld">.com</span></p>
  <div class="services centered" style="top:478px;">
    <ul class="service-list" style="font-size:25px;">
      <li>Moisture</li><li>Mold</li><li>Odor</li><li>Duct Cleaning</li>
    </ul>
    <span class="sign-off" style="font-size:33px;">Happy<br>Designing!!</span>
  </div>
</section>

</body>
</html>
```